Business card for event manager / organizer "waiter service"

Draft of a new valuable business card for my company.
Events, personnel service providers, festivals

```html
<!DOCTYPE html>
<html lang="de">
<head>
<meta charset="utf-8">
<title>Niko's Kellnerservice – Visitenkarte</title>
<link rel="stylesheet" href="https://fonts.googleapis.com/css2?family=Poppins:wght@300;400;600;700&display=swap">
<style>
  :root {
    --page-bg: #3a3a3c;
    --card-bg: #1c1c1d;
    --orange: #ef7f1f;
    --white: #ffffff;
    --muted: #d8d8d8;
    --photo-light: #d9dbe0;
    --photo-dark: #141414;
  }
  * { box-sizing: border-box; margin: 0; padding: 0; }
  html, body { width: 1200px; height: 900px; overflow: hidden; }
  body {
    background: var(--page-bg);
    font-family: "Poppins", sans-serif;
    color: var(--white);
    display: flex;
    flex-direction: column;
    align-items: center;
    justify-content: center;
    gap: 40px;
  }
  .card {
    width: 640px;
    height: 376px;
    border-radius: 22px;
    background: var(--card-bg);
    position: relative;
    overflow: hidden;
  }

  /* Front side */
  .card--front {
    display: flex;
    align-items: center;
    justify-content: center;
  }
  .brand {
    display: flex;
    align-items: center;
    gap: 22px;
  }
  .brand__square {
    width: 96px;
    height: 96px;
    background: var(--orange);
    flex: none;
  }
  .brand__text { display: flex; flex-direction: column; }
  .brand__name {
    font-weight: 700;
    color: var(--white);
    text-transform: uppercase;
    line-height: 1.05;
    letter-spacing: 0.5px;
  }
  .card--front .brand__name { font-size: 40px; }
  .brand__tagline {
    font-weight: 300;
    color: var(--white);
    margin-top: 8px;
  }
  .card--front .brand__tagline { font-size: 17px; }

  /* Back side */
  .card--back { display: flex; }
  .portrait {
    width: 46%;
    height: 100%;
    background: radial-gradient(ellipse at 45% 35%, var(--photo-light) 0%, #8d8f94 45%, var(--photo-dark) 100%);
  }
  .details {
    flex: 1;
    padding: 28px 30px 0 26px;
    background: linear-gradient(90deg, #262626 0%, var(--card-bg) 40%);
  }
  .details .brand { gap: 10px; margin-bottom: 22px; }
  .details .brand__square { width: 38px; height: 38px; }
  .details .brand__name { font-size: 16px; }
  .details .brand__tagline { font-size: 8px; margin-top: 3px; }
  .person__name {
    font-weight: 600;
    font-size: 27px;
    color: var(--orange);
    line-height: 1.1;
  }
  .person__role {
    font-weight: 300;
    font-size: 15px;
    color: var(--muted);
    margin: 4px 0 18px;
  }
  .contact { list-style: none; }
  .contact__item {
    display: flex;
    align-items: center;
    gap: 9px;
    font-size: 13.5px;
    font-weight: 400;
    line-height: 1;
    margin-bottom: 10px;
    white-space: nowrap;
  }
  .contact__icon { width: 14px; height: 14px; flex: none; fill: var(--orange); }
</style>
</head>
<body>

  <section class="card card--front" aria-label="Vorderseite">
    <div class="brand">
      <div class="brand__square"></div>
      <div class="brand__text">
        <span class="brand__name">Niko's<br>Kellnerservice</span>
        <span class="brand__tagline">...denn die nächste Feier kommt bestimmt!</span>
      </div>
    </div>
  </section>

  <section class="card card--back" aria-label="Rückseite">
    <div class="portrait" role="img" aria-label="Foto des Inhabers in Kellnerweste und Fliege mit einem Tablett voller Sektgläser"></div>
    <div class="details">
      <div class="brand">
        <div class="brand__square"></div>
        <div class="brand__text">
          <span class="brand__name">Niko's Kellnerservice</span>
          <span class="brand__tagline">...denn die nächste Feier kommt bestimmt!</span>
        </div>
      </div>
      <h1 class="person__name">Niko Brandtner</h1>
      <p class="person__role">Inhaber</p>
      <ul class="contact">
        <li class="contact__item">
          <svg class="contact__icon" viewBox="0 0 16 16"><path d="M3.5 1.5l2.5 3-1.5 1.5c.8 2 2.5 3.7 4.5 4.5l1.5-1.5 3 2.5-1.5 2.5C7 14 2 9 1 3z"/></svg>
          02361 555 01 42
        </li>
        <li class="contact__item">
          <svg class="contact__icon" viewBox="0 0 16 16"><path d="M3.5 1.5l2.5 3-1.5 1.5c.8 2 2.5 3.7 4.5 4.5l1.5-1.5 3 2.5-1.5 2.5C7 14 2 9 1 3z"/></svg>
          0170 555 23 47
        </li>
        <li class="contact__item">
          <svg class="contact__icon" viewBox="0 0 16 16"><circle cx="8" cy="8" r="6.5" fill="none" stroke="#ef7f1f" stroke-width="1.6"/><path d="M1.5 8h13M8 1.5c-3 3.5-3 9.5 0 13M8 1.5c3 3.5 3 9.5 0 13" fill="none" stroke="#ef7f1f" stroke-width="1.2"/></svg>
          www.nikos-kellnerservice.de
        </li>
        <li class="contact__item">
          <svg class="contact__icon" viewBox="0 0 16 16"><path d="M1 3h14v10H1z"/><path d="M1 3l7 6 7-6" fill="none" stroke="#1c1c1d" stroke-width="1.3"/></svg>
          info@nikos-kellnerservice.de
        </li>
        <li class="contact__item">
          <svg class="contact__icon" viewBox="0 0 16 16"><path d="M8 0.5a5 5 0 0 1 5 5c0 3.8-5 10-5 10s-5-6.2-5-10a5 5 0 0 1 5-5z"/><circle cx="8" cy="5.5" r="1.8" fill="#1c1c1d"/></svg>
          Lindenweg 14, 45700 Feldbach
        </li>
        <li class="contact__item">
          <svg class="contact__icon" viewBox="0 0 16 16"><rect x="1" y="1" width="14" height="14" rx="2"/></svg>
          www.social.example/nikoskellnerservice
        </li>
      </ul>
    </div>
  </section>

</body>
</html>
```